Cove medical spa and wellness

Integrate existing logo and web design (colors and background) into tri fold, single card brochure and business card design. We already have a logo and an idea for our promotional material but we would like someone to bring it together for us! Covewellnessandspa.com. We want to see what a marble background with a faded lily (as seen on our webpage) would look like on brochures and business cards.

```html
<!DOCTYPE html>
<html lang="en">
<head>
<meta charset="utf-8">
<title>Cove Medical Spa &amp; Wellness — Business Card</title>
<link rel="stylesheet" href="https://fonts.googleapis.com/css2?family=Jost:wght@400;500&family=Yellowtail&display=swap">
<style>
  :root {
    --backdrop: #1c1c1d;
    --card: #2c2c2e;
    --card-edge: #232325;
    --gold: #d9a928;
    --silver: #c8c8ca;
    --ink-light: #f2f2f2;
  }
  * { box-sizing: border-box; margin: 0; padding: 0; }
  html, body {
    width: 1200px; height: 960px; overflow: hidden;
    background: var(--backdrop);
  }
  .canvas {
    position: relative; width: 1200px; height: 960px;
    display: flex; flex-direction: column; align-items: center; justify-content: center; gap: 56px;
  }
  .card {
    position: relative; width: 700px; height: 400px;
    background: var(--card);
    border: 1px solid var(--card-edge);
    box-shadow: 0 18px 40px rgba(0,0,0,.55);
  }
  /* front: brand name */
  .card--front { display: flex; align-items: center; justify-content: center; }
  .brand-lockup { display: flex; align-items: center; gap: 18px; }
  .brand-lockup__dot {
    width: 22px; height: 22px; border-radius: 50%; background: var(--silver);
  }
  .brand-lockup__name {
    font-family: "Jost", sans-serif; font-weight: 400; font-size: 34px;
    letter-spacing: 0.12em; text-transform: uppercase; color: var(--silver);
  }
  /* back: contact details */
  .card__brand {
    position: absolute; top: 78px; right: 70px;
    display: flex; align-items: center; gap: 14px;
  }
  .card__brand-dot { width: 18px; height: 18px; border-radius: 50%; background: var(--gold); }
  .card__brand-name {
    font-family: "Jost", sans-serif; font-weight: 500; font-size: 40px;
    letter-spacing: 0.08em; color: var(--gold);
  }
  .contact { position: absolute; left: 62px; bottom: 46px; }
  .contact__name {
    font-family: "Yellowtail", cursive; font-size: 40px; color: var(--gold);
    margin-bottom: 10px;
  }
  .contact__address, .contact__line {
    font-family: "Jost", sans-serif; font-size: 18px; color: var(--ink-light); line-height: 1.3;
  }
  .contact__address { margin-bottom: 12px; }
  .contact__line { display: flex; align-items: center; gap: 10px; }
  .contact__icon { width: 16px; height: 16px; flex: none; }
</style>
</head>
<body>
<main class="canvas">
  <section class="card card--front" aria-label="Business card front">
    <div class="brand-lockup">
      <span class="brand-lockup__dot"></span>
      <span class="brand-lockup__name">Cove Medical Spa &amp; Wellness</span>
    </div>
  </section>

  <section class="card card--back" aria-label="Business card back">
    <div class="card__brand">
      <span class="card__brand-dot"></span>
      <span class="card__brand-name">Cove</span>
    </div>
    <div class="contact">
      <p class="contact__name">Daniel Brooks</p>
      <p class="contact__address">2140 W. Harbor Lane, Suite 12<br>Mesa, AZ 85201</p>
      <p class="contact__line">
        <svg class="contact__icon" viewBox="0 0 16 16" aria-hidden="true"><path fill="var(--gold)" d="M3.6 1.5l2.3 2.6-1.3 1.8c.9 2 2.5 3.6 4.5 4.5l1.8-1.3 2.6 2.3-1.3 2.3C7 13.9 2.1 9 1.3 2.8z"/></svg>
        (602) 555-0142
      </p>
      <p class="contact__line">
        <svg class="contact__icon" viewBox="0 0 16 16" aria-hidden="true"><rect x="1" y="3" width="14" height="10" fill="var(--gold)"/><path d="M1.5 3.5L8 9l6.5-5.5" fill="none" stroke="var(--card)" stroke-width="1.3"/></svg>
        welcome@covewellnessandspa.com
      </p>
      <p class="contact__line">
        <svg class="contact__icon" viewBox="0 0 16 16" aria-hidden="true"><circle cx="8" cy="8" r="7" fill="var(--gold)"/><path d="M1 8h14M8 1c-3 3.5-3 10.5 0 14M8 1c3 3.5 3 10.5 0 14" fill="none" stroke="var(--card)" stroke-width="1"/></svg>
        www.covewellnessandspa.com
      </p>
    </div>
  </section>
</main>
</body>
</html>
```